Need help in designing new business card utilizing our new logo.

BuildMark Solutions works with Construction Business Owners, Managers & IT Professionals to strengthen software usage and increase user productivity.

Our Construction Accounting and Mobile Field Management Software Clients engage with us in the following areas:

New Software Implementations
Software Re-Implementations
Redesigning Software Usage at the User Level
Project Coordination & Management
Continued Software Support

Old tag line:
Weighing Options - Implementing Solutions

www.buildmark-solutions.example

Ridge 4 is a product, but not needed for a new business card.

```html
<!DOCTYPE html>
<html lang="en">
<head>
<meta charset="utf-8">
<title>BuildMark Solutions – Business Card</title>
<link href="https://fonts.googleapis.com/css2?family=Arimo:wght@400;700&family=Montserrat:wght@600&display=swap" rel="stylesheet">
<style>
  :root {
    --backdrop: #e9e6e7;
    --card-white: #ffffff;
    --card-grey: #7a7a7c;
    --pattern-light: #8a8a8c;
    --pattern-dark: #747476;
    --brand-blue: #2222a6;
    --text-grey: #8a8a8a;
    --band-grey: #9a9a9a;
  }
  * { box-sizing: border-box; margin: 0; padding: 0; }
  html, body { width: 1200px; height: 675px; overflow: hidden; }
  body {
    background: var(--backdrop);
    font-family: "Arimo", Arial, sans-serif;
    position: relative;
  }
  .card {
    position: absolute;
    top: 189px;
    width: 520px;
    height: 297px;
    overflow: hidden;
    box-shadow: 0 6px 18px rgba(0,0,0,0.18);
  }
  .card--front { left: 50px; background: var(--card-white); }
  .card--back { left: 630px; background: var(--card-grey); }

  .brand {
    position: absolute;
    display: flex;
    align-items: center;
    gap: 12px;
    font-family: "Montserrat", Arial, sans-serif;
    font-weight: 600;
    white-space: nowrap;
  }
  .brand__mark { display: block; flex: none; }
  .card--front .brand { left: 240px; top: 44px; font-size: 22px; color: var(--brand-blue); }
  .card--front .brand__mark { width: 24px; height: 24px; background: var(--brand-blue); }

  .contact {
    position: absolute;
    left: 272px;
    top: 104px;
    width: 240px;
    font-size: 12.5px;
    color: var(--text-grey);
    line-height: 1.55;
    white-space: nowrap;
  }
  .contact__row { display: flex; align-items: center; gap: 7px; }
  .contact__icon { width: 16px; height: 16px; flex: none; }
  .contact__address { margin-top: 8px; padding-left: 23px; }
  .contact__web { margin-top: 10px; padding-left: 23px; }
  .contact__web strong { color: var(--brand-blue); font-weight: 700; }

  .person { position: absolute; left: 34px; top: 196px; white-space: nowrap; }
  .person__name {
    font-size: 19px;
    font-weight: 700;
    color: var(--brand-blue);
    letter-spacing: 0.3px;
    text-transform: uppercase;
  }
  .person__role { font-size: 13px; color: var(--text-grey); margin-top: 2px; }

  .band { position: absolute; bottom: 0; }
  .band--grey { left: 0; width: 62%; height: 12px; background: var(--band-grey); }
  .band--blue { right: 0; width: 38%; height: 20px; background: var(--brand-blue); }

  .card__pattern {
    position: absolute;
    inset: 0;
    background: radial-gradient(ellipse at 40% 45%, var(--pattern-light), var(--pattern-dark) 75%);
  }
  .card--back .brand {
    left: 50%; top: 50%;
    transform: translate(-50%, -50%);
    font-size: 34px;
    color: #ffffff;
  }
  .card--back .brand__mark { width: 34px; height: 34px; background: var(--brand-blue); }
</style>
</head>
<body>
  <section class="card card--front" aria-label="Business card front">
    <div class="brand">
      <span class="brand__mark" aria-hidden="true"></span>
      <span class="brand__name">BuildMark Solutions</span>
    </div>

    <div class="contact">
      <div class="contact__row">
        <svg class="contact__icon" viewBox="0 0 20 20" aria-hidden="true">
          <circle cx="10" cy="10" r="10" fill="var(--brand-blue)"/>
          <path d="M6.5 5.5c.6-.4 1.3-.3 1.6.3l.8 1.5c.2.5.1 1-.3 1.3l-.6.5c.5 1.2 1.4 2.1 2.6 2.6l.5-.6c.3-.4.9-.5 1.3-.3l1.5.8c.6.3.7 1 .3 1.6l-.6.8c-.5.6-1.4.8-2.1.5-2.6-1-4.6-3-5.6-5.6-.3-.7-.1-1.6.5-2.1z" fill="#fff"/>
        </svg>
        <span>555-014-2280</span>
      </div>
      <div class="contact__row">
        <svg class="contact__icon" viewBox="0 0 20 20" aria-hidden="true">
          <circle cx="10" cy="10" r="10" fill="var(--brand-blue)"/>
          <rect x="5" y="6.5" width="10" height="7" fill="none" stroke="#fff" stroke-width="1.3"/>
          <path d="M5 6.5l5 4 5-4" fill="none" stroke="#fff" stroke-width="1.3"/>
        </svg>
        <span>jmarlow@buildmark-solutions.example</span>
      </div>
      <div class="contact__address">
        14B Orchard Lane - Suite 120<br>
        Millbrook Falls NY 10000
      </div>
      <div class="contact__web">www.<strong>buildmark-solutions</strong>.example</div>
    </div>

    <div class="person">
      <div class="person__name">Jordan M. Marlow</div>
      <div class="person__role">Owner</div>
    </div>

    <div class="band band--grey"></div>
    <div class="band band--blue"></div>
  </section>

  <section class="card card--back" aria-label="Business card back">
    <div class="card__pattern" role="img" aria-label="Faint grey pixel-block map pattern across the card"></div>
    <div class="brand">
      <span class="brand__mark" aria-hidden="true"></span>
      <span class="brand__name">BuildMark Solutions</span>
    </div>
  </section>
</body>
</html>
```